I would like a single page website for Skyward Rentals Pacific. In the file list provided there is basic information to be included as well as our logo with colors, fonts and images to be included.
Site must be very simple and be able to be loaded onto smart phones etc very quickly.
Site needs to be very smart in appearance

Target Market(s)

All prospective drone customers from Police to Parties.

Industry/Entity Type

Hire

Requirements
Must have
• Must have variation of color schemes supplied
Nice to have
• Must be very eye catching without going over the top
Should not have
• Anything slow to load.

```html
<!DOCTYPE html>
<html lang="en">
<head>
<meta charset="utf-8">
<title>Skyward Rentals Pacific</title>
<link href="https://fonts.googleapis.com/css2?family=Raleway:wght@400;600;700&family=Open+Sans:wght@400;600&display=swap" rel="stylesheet">
<style>
:root{
  --green:#8cc63f;
  --green-dark:#6fa82a;
  --ink:#333;
  --muted:#777;
  --dark:#3d3d3d;
  --darker:#2e2e2e;
  --nav:#e9e9e9;
  --light:#f2f2f2;
  --white:#fff;
}
*{box-sizing:border-box;margin:0;padding:0}
html,body{width:703px;height:1200px;overflow:hidden}
body{font-family:"Open Sans",sans-serif;color:var(--ink);background:var(--white);font-size:8px;line-height:1.5}
h1,h2,h3{font-family:"Raleway",sans-serif}
.wrap{width:600px;margin:0 auto;position:relative}

.site-header{height:33px}
.site-header .wrap{display:flex;justify-content:space-between;align-items:center;height:33px}
.brand{display:flex;align-items:center;gap:6px;font-family:"Raleway",sans-serif;font-weight:700;font-size:11px;color:var(--green);letter-spacing:.5px;text-transform:uppercase}
.brand-dot{width:10px;height:10px;border-radius:50%;background:var(--green)}
.call{display:flex;align-items:center;gap:6px;font-size:7.5px;color:var(--muted)}
.call-icon{width:16px;height:16px;border-radius:50%;background:var(--green);display:flex;align-items:center;justify-content:center}

.main-nav{height:18px;background:var(--nav);border-top:1px solid #ddd;border-bottom:1px solid #ddd}
.main-nav ul{list-style:none;display:flex;height:18px;align-items:center}
.main-nav li{font-size:6.5px;font-weight:600;padding:0 18px;height:18px;line-height:18px;color:#555;text-transform:uppercase}
.main-nav li.active{background:var(--green);color:var(--white)}
.main-nav .search{margin-left:auto;padding:0 8px}

.hero{position:relative;height:362px;overflow:hidden}
.hero-photo{position:absolute;inset:0;background:linear-gradient(160deg,#9fb7cf 0%,#6f8aa6 35%,#556677 60%,#3a3f44 100%)}
.hero-content{position:relative;padding-top:70px}
.hero h1{color:var(--white);font-size:28px;font-weight:600;letter-spacing:.5px}
.hero p{color:#eef;font-size:8px;width:230px;margin:6px 0 12px;text-transform:uppercase}
.btn{display:inline-block;background:var(--green);color:var(--white);font-size:6.5px;font-weight:600;padding:4px 10px;text-transform:uppercase;border-radius:2px}
.hero-curve{position:absolute;left:0;bottom:0;width:703px;height:60px}

.about{background:var(--dark);color:#ddd;text-align:center;height:110px;padding-top:12px}
.about h2{color:var(--white);font-size:17px;font-weight:600}
.about .lead{font-size:7.5px;margin:4px 0 6px}
.about .body{font-size:6px;color:#aaa;width:540px;margin:0 auto 8px}

.services{padding-top:26px;height:280px}
.section-title{font-size:16px;font-weight:600;color:#444}
.rule{width:600px;height:1px;background:#ddd;margin:4px 0 4px}
.services .sub{font-size:7px;color:var(--muted)}
.cards{display:flex;justify-content:space-between;margin-top:34px}
.card{width:186px;height:150px;border:1px solid #ddd;padding:42px 12px 0;position:relative}
.card-icon{position:absolute;top:-22px;left:50%;margin-left:-24px;width:48px;height:48px;border-radius:50%;background:var(--green);border:4px solid #e4f2d2;display:flex;align-items:center;justify-content:center}
.card h3{color:var(--green);font-size:8px;font-weight:600;text-transform:uppercase}
.card p{font-size:6px;color:var(--muted);margin:3px 0 8px}

.what{background:var(--light);height:310px;padding-top:26px}
.what .lead{font-size:7.5px;color:#555;width:250px;margin:8px 0 10px}
.feature-list{list-style:none;width:280px}
.feature-list li{font-size:6px;color:#555;display:flex;align-items:center;gap:6px;margin-bottom:7px}
.feature-list li::before{content:"";width:7px;height:7px;border-radius:50%;background:var(--green);flex:none}
.video{position:absolute;right:0;top:60px;width:230px;height:190px;background:#111;border:4px solid #222}
.video-frame{position:absolute;inset:0 0 16px 0;background:radial-gradient(ellipse at 50% 40%,#8fa8c0 0%,#3b566b 40%,#2f6b3a 75%,#1a1a1a 100%)}
.video-bar{position:absolute;left:0;right:0;bottom:0;height:16px;background:#1b1b1b;display:flex;align-items:center;padding:0 6px;gap:6px}
.video-bar .track{flex:1;height:2px;background:#555}

.site-footer{background:var(--darker);height:80px;color:#aaa;padding-top:20px}
.site-footer .wrap{display:flex;justify-content:space-between}
.foot-nav{list-style:none;display:flex;gap:14px;font-size:6.5px;color:#ccc}
.copy{font-size:5.5px;margin-top:6px;color:#888}
.social{display:flex;align-items:center;gap:5px;font-size:6.5px;color:#ccc}
.social span.c{width:16px;height:16px;border-radius:50%;display:inline-block}
</style>
</head>
<body>

<header class="site-header">
  <div class="wrap">
    <div class="brand"><span class="brand-dot"></span>Skyward Rentals Pacific</div>
    <div class="call">
      <span class="call-icon"><svg width="8" height="8" viewBox="0 0 24 24"><path fill="#fff" d="M6.6 10.8a15 15 0 0 0 6.6 6.6l2.2-2.2a1 1 0 0 1 1-.25 11.4 11.4 0 0 0 3.6.57 1 1 0 0 1 1 1V20a1 1 0 0 1-1 1A17 17 0 0 1 3 4a1 1 0 0 1 1-1h3.5a1 1 0 0 1 1 1c0 1.25.2 2.45.57 3.57a1 1 0 0 1-.25 1z"/></svg></span>
      CALL US: 1300 555 014
    </div>
  </div>
</header>

<nav class="main-nav">
  <ul class="wrap">
    <li class="active">Home</li><li>About Us</li><li>Services</li><li>What We Do</li><li>Video</li><li>Contact Us</li>
    <li class="search"><svg width="7" height="7" viewBox="0 0 24 24"><circle cx="10" cy="10" r="7" fill="none" stroke="#555" stroke-width="3"/><path d="M15 15l7 7" stroke="#555" stroke-width="3"/></svg></li>
  </ul>
</nav>

<section class="hero">
  <div class="hero-photo" role="img" aria-label="White camera drone hovering in front of a construction site with tower cranes"></div>
  <div class="wrap hero-content">
    <h1>WE ARE GIVE DRONES</h1>
    <p>Simply dummy text of the printing and typesetting industry. Lorem ipsum has been the industry's standard dummy text.</p>
    <span class="btn">View More Info</span>
  </div>
  <svg class="hero-curve" viewBox="0 0 703 60" preserveAspectRatio="none">
    <path d="M0 10 Q300 70 703 20 L703 60 L0 60Z" fill="#8cc63f"/>
    <path d="M0 26 Q320 80 703 36 L703 60 L0 60Z" fill="#3d3d3d"/>
  </svg>
</section>

<section class="about">
  <h2>ABOUT US</h2>
  <p class="lead">Simply dummy text of the printing and typesetting industry. Lorem Ipsum has been the industry's standard dummy text ever since.</p>
  <p class="body">Sed ut perspiciatis unde omnis iste natus error sit voluptatem accusantium doloremque laudantium, totam rem aperiam, eaque ipsa quae ab illo inventore veritatis et quasi architecto beatae vitae dicta sunt explicabo. Nemo enim ipsam voluptatem quia voluptas sit aspernatur aut odit aut fugit, sed quia consequuntur magni dolores.</p>
  <span class="btn">Read More</span>
</section>

<section class="services">
  <div class="wrap">
    <h2 class="section-title">SERVICES</h2>
    <div class="rule"></div>
    <p class="sub">Simply dummy text of the printing and typesetting industry. Lorem Ipsum has been the industry's standard dummy text ever since.</p>
    <div class="cards">
      <article class="card">
        <div class="card-icon"><svg width="22" height="22" viewBox="0 0 24 24"><path fill="#fff" d="M6 2h1.5v6h1V2H10v6h1V2h1.5v7a3 3 0 0 1-2.5 3v10H8V12a3 3 0 0 1-2.5-3V2zM15 2c2.5 0 3.5 3 3.5 7v4H17v9h-2z"/></svg></div>
        <h3>Parties</h3>
        <p>Lorem ipsum dolor sit amet, consectetur adipiscing elit, sed do eiusmod tempor incididunt ut labore et dolore magna aliqua. Ut enim.</p>
        <span class="btn">Read More</span>
      </article>
      <article class="card">
        <div class="card-icon"><svg width="24" height="24" viewBox="0 0 24 24"><path fill="#fff" d="M12 5C6 5 2 12 2 12s4 7 10 7 10-7 10-7-4-7-10-7zm0 11a4 4 0 1 1 0-8 4 4 0 0 1 0 8z"/><circle cx="12" cy="12" r="2" fill="#fff"/></svg></div>
        <h3>Surveillance</h3>
        <p>Lorem ipsum dolor sit amet, consectetur adipiscing elit, sed do eiusmod tempor incididunt ut labore et dolore magna aliqua. Ut enim.</p>
        <span class="btn">Read More</span>
      </article>
      <article class="card">
        <div class="card-icon"><svg width="22" height="22" viewBox="0 0 24 24"><path fill="#fff" d="M12 2l8 3v6c0 5-3.5 9.5-8 11-4.5-1.5-8-6-8-11V5z"/></svg></div>
        <h3>Security</h3>
        <p>Lorem ipsum dolor sit amet, consectetur adipiscing elit, sed do eiusmod tempor incididunt ut labore et dolore magna aliqua. Ut enim.</p>
        <span class="btn">Read More</span>
      </article>
    </div>
  </div>
</section>

<section class="what">
  <div class="wrap">
    <h2 class="section-title">WHAT WE DO</h2>
    <div class="rule"></div>
    <p class="lead">Simply dummy text of the printing and typesetting industry. Lorem Ipsum has been the industry's standard dummy text ever since.</p>
    <ul class="feature-list">
      <li>Special Occasions, Children's Birthday Parties, Weddings</li>
      <li>Sporting events – all – Views of yourself participating in sports</li>
      <li>Real Estate Brochures</li>
      <li>Construction project updates for owners and builders</li>
      <li>Surveillance – Crime, Lease records and traffic</li>
      <li>Building Roof Condition Inspections</li>
      <li>Accident reconstruction</li>
      <li>Insurance assessing</li>
    </ul>
    <div class="video">
      <div class="video-frame" role="img" aria-label="Video still of a drone flying over a floodlit sports stadium"></div>
      <div class="video-bar">
        <svg width="7" height="7" viewBox="0 0 10 10"><path d="M1 0l9 5-9 5z" fill="#ccc"/></svg>
        <span class="track"></span>
      </div>
    </div>
  </div>
</section>

<footer class="site-footer">
  <div class="wrap">
    <div>
      <ul class="foot-nav"><li>Home</li><li>About Us</li><li>Services</li><li>Features</li><li>Video</li><li>Contact Us</li></ul>
      <p class="copy">Copyright © Skyward Rentals Pacific. All Rights Reserved.</p>
    </div>
    <div class="social">Connect With Us
      <span class="c" style="background:#3fa9e0"></span>
      <span class="c" style="background:#3fa9e0"></span>
      <span class="c" style="background:#3b5998"></span>
      <span class="c" style="background:#8cc63f"></span>
    </div>
  </div>
</footer>

</body>
</html>
```